International business needs business cards

Our company, DRV Ventures Inc. is in the business of supplying a range construction products with particular emphasis on CEMENT. We have developed our own brand - TORVAN SUPPLIES - with which to infiltrate the market. We are launching our brand of cement (TORVAN Type IS Cement) into the Caribbean which is unlike anything this market has ever seen. A monopoly has existed here for the past 60-odd years and the market has now opened to allow the importation of other brands and consumers are anxious and ready for change/improvement. We are very excited to be launching and want to make a great first impression. We will be conducting workshops and seminars (from government level to the hardware store owners) and we want our business card to give us the strong, confident introduction that we need.

Target Market(s)

construction; builders; engineers; home owners

Industry/Entity Type

Construction

Contact Information for Business Card

Marisol Depree
CEO
cell # 1 555 4180736
Ground floor,Lindell Plaza Suite 2734
George Town,Grand Cayman
Cayman Islands,KY1-4823
EMAIL: m.depree@drvventuresinc.example
web site drvventuresinc.example

COMPANY: skype info drv.ventures.example

second card
Yvette Brannock-Depree
CFO
CELL# 1 555 607 3941
George Town,Grand Cayman
Cayman Islands,KY1-4823
EMAIL: y.brannockdepree@drvventuresinc.example
website drvventuresinc.example

Requirements
Must have
• Business cards must display BOTH logos - DRV is the company and TORVAN is the brand.

```html
<!DOCTYPE html>
<html lang="en">
<head>
<meta charset="utf-8">
<title>DRV Ventures Inc. — Business Card</title>
<link rel="stylesheet" href="https://fonts.googleapis.com/css2?family=Roboto:wght@300;400;700&display=swap">
<style>
  :root {
    --bg: #e9e6e1;
    --wine: #7d1419;
    --wine-dark: #5c0d11;
    --wine-light: #94232a;
    --ink: #111111;
    --paper: #ffffff;
    --text-grey: #666666;
    --crest-grey: #8a8a8a;
  }
  * { margin: 0; padding: 0; box-sizing: border-box; }
  html, body {
    width: 1200px; height: 950px; overflow: hidden;
    background: var(--bg);
    font-family: "Roboto", Arial, sans-serif;
  }
  .card {
    position: absolute; left: 240px;
    width: 720px; height: 411px;
    box-shadow: 0 10px 28px rgba(0,0,0,.28);
  }
  /* back side */
  .card--back {
    top: 40px;
    background: linear-gradient(135deg, var(--wine-light), var(--wine) 50%, var(--wine-dark));
    display: flex; flex-direction: column; align-items: center; justify-content: center;
    color: var(--paper);
  }
  .back-mark {
    display: flex; align-items: center; gap: 14px;
    border: 2px solid rgba(255,255,255,.85);
    padding: 22px 28px;
  }
  .back-mark__square { width: 26px; height: 26px; background: var(--paper); }
  .back-mark__name { font-size: 40px; font-weight: 700; letter-spacing: 2px; }
  .back-url {
    margin-top: 70px; font-size: 17px; font-weight: 300; letter-spacing: 5px;
  }
  /* front side */
  .card--front { top: 496px; background: var(--paper); overflow: hidden; }
  .brand {
    position: absolute; left: 420px; top: 40px;
    display: flex; align-items: center; gap: 14px;
  }
  .brand__square { width: 96px; height: 96px; background: var(--wine); }
  .brand__name { font-size: 30px; font-weight: 700; color: var(--ink); line-height: 1; }
  .name-band {
    position: absolute; left: 0; top: 96px;
    width: 420px; height: 68px; background: var(--ink);
    color: var(--paper); padding: 10px 0 0 40px;
  }
  .name-band__name { font-size: 24px; font-weight: 700; }
  .name-band__title { font-size: 15px; font-weight: 300; margin-top: 2px; }
  .product-brand {
    position: absolute; right: 36px; top: 168px;
    width: 190px; display: flex; align-items: center; gap: 10px;
  }
  .product-brand__circle { width: 22px; height: 22px; border-radius: 50%; background: var(--crest-grey); flex: none; }
  .product-brand__name { font-size: 20px; font-weight: 700; color: var(--crest-grey); line-height: 1.1; }
  .address {
    position: absolute; left: 40px; top: 196px;
    font-size: 15px; font-weight: 300; color: var(--text-grey); line-height: 1.3;
  }
  .contacts {
    position: absolute; left: 40px; top: 296px;
    list-style: none; font-size: 15px; font-weight: 300; color: var(--text-grey);
  }
  .contacts li { display: flex; align-items: center; gap: 10px; height: 24px; }
  .contacts svg { width: 14px; height: 14px; fill: var(--wine); flex: none; }
</style>
</head>
<body>
  <section class="card card--back" aria-label="Card back">
    <div class="back-mark">
      <span class="back-mark__square"></span>
      <span class="back-mark__name">DRV</span>
    </div>
    <p class="back-url">www.drvventuresinc.example</p>
  </section>

  <section class="card card--front" aria-label="Card front">
    <div class="brand">
      <span class="brand__square"></span>
      <span class="brand__name">DRV Ventures Inc.</span>
    </div>

    <div class="name-band">
      <p class="name-band__name">Marisol Depree</p>
      <p class="name-band__title">CEO</p>
    </div>

    <div class="product-brand">
      <span class="product-brand__circle"></span>
      <span class="product-brand__name">TORVAN SUPPLIES</span>
    </div>

    <p class="address">
      Ground floor<br>
      Lindell Plaza Suite 2734<br>
      George Town,Grand Cayman<br>
      Cayman Islands,KY1-4823
    </p>

    <ul class="contacts">
      <li>
        <svg viewBox="0 0 14 14" aria-hidden="true"><path d="M4 0h6a1 1 0 0 1 1 1v12a1 1 0 0 1-1 1H4a1 1 0 0 1-1-1V1a1 1 0 0 1 1-1zm0.5 2v8.5h5V2z"/></svg>
        1 555 4180736
      </li>
      <li>
        <svg viewBox="0 0 14 14" aria-hidden="true"><path d="M0 3h14v8H0z M0 3l7 5 7-5" stroke="#fff" stroke-width="1"/></svg>
        m.depree@drvventuresinc.example
      </li>
      <li>
        <svg viewBox="0 0 14 14" aria-hidden="true"><circle cx="7" cy="7" r="7"/><path d="M1 7h12M7 1c-3 3-3 9 0 12M7 1c3 3 3 9 0 12" stroke="#fff" stroke-width="1" fill="none"/></svg>
        drvventuresinc.example
      </li>
    </ul>
  </section>
</body>
</html>
```